BOLD & MINIMALIST DESIGN NEEDED

We want a very bold but minimalistic business card design that is impactful and utilizes both sides of the business card. Our current logo is included for your use.

We want bold fonts and good use of negative space. We don't want the logo to overpower the design.

Target Market(s)

Professionals who are building new commercial buildings.

Industry/Entity Type

Construction

Contact Information for Business Card

Name, Title, email, office phone, cell phone, website

Font styles to use
Serif
Sans Serif

Requirements
Must have
• Bold design!

```html
<!DOCTYPE html>
<html lang="en">
<head>
<meta charset="utf-8">
<title>Ridgeline Design + Build — Business Card</title>
<link href="https://fonts.googleapis.com/css2?family=Poppins:wght@400;600;700&display=swap" rel="stylesheet">
<style>
  :root {
    --stage: #d9d3c9;
    --card-white: #ffffff;
    --card-black: #050505;
    --ink: #1a1a1a;
    --green: #8dc63f;
    --white: #ffffff;
  }
  * { margin: 0; padding: 0; box-sizing: border-box; }
  html, body {
    width: 916px;
    height: 1200px;
    overflow: hidden;
    background: var(--stage);
    font-family: "Poppins", Arial, sans-serif;
  }
  .canvas {
    position: relative;
    width: 916px;
    height: 1200px;
  }
  .card {
    position: absolute;
    left: 73px;
    width: 770px;
    height: 460px;
    border-radius: 24px;
    overflow: hidden;
    box-shadow: 0 6px 18px rgba(0, 0, 0, 0.25);
  }
  .card--front { top: 108px; background: var(--card-white); }
  .card--back  { top: 641px; background: var(--card-black); }

  /* Company name */
  .company {
    position: absolute;
    font-weight: 700;
    text-transform: uppercase;
    line-height: 1;
  }
  .company__name { display: block; letter-spacing: 1px; }
  .company__tag  { display: block; letter-spacing: 7px; }

  .card--front .company {
    left: 39px;
    top: 62px;
    color: var(--ink);
  }
  .card--front .company__name { font-size: 50px; }
  .card--front .company__tag  { font-size: 19px; margin-top: 8px; padding-left: 36px; }

  .card--back .company {
    left: 0;
    right: 0;
    top: 262px;
    text-align: center;
    color: var(--white);
  }
  .card--back .company__name { font-size: 52px; }
  .card--back .company__tag  { font-size: 19px; margin-top: 10px; }

  /* Person */
  .person {
    position: absolute;
    right: 46px;
    top: 72px;
    text-align: right;
  }
  .person__name {
    font-weight: 600;
    font-size: 27px;
    color: var(--green);
    line-height: 1.1;
  }
  .person__title {
    font-weight: 400;
    font-size: 16px;
    color: var(--ink);
    margin-top: 4px;
  }

  /* Contact list */
  .contacts {
    position: absolute;
    left: 30px;
    top: 331px;
    list-style: none;
  }
  .contacts__item {
    display: flex;
    align-items: center;
    height: 25.5px;
    font-size: 17px;
    color: var(--ink);
  }
  .contacts__icon {
    width: 17px;
    height: 17px;
    margin-right: 10px;
    fill: var(--green);
    flex: none;
  }
</style>
</head>
<body>
<main class="canvas">

  <section class="card card--front" aria-label="Business card front">
    <div class="company">
      <span class="company__name">Ridgeline</span>
      <span class="company__tag">Design + Build</span>
    </div>

    <div class="person">
      <p class="person__name">Daniel Brooks</p>
      <p class="person__title">CEO &amp; Founder</p>
    </div>

    <ul class="contacts">
      <li class="contacts__item">
        <svg class="contacts__icon" viewBox="0 0 24 24" aria-hidden="true"><path d="M6.6 10.8a15.1 15.1 0 0 0 6.6 6.6l2.2-2.2a1 1 0 0 1 1-.25 11.4 11.4 0 0 0 3.6.57 1 1 0 0 1 1 1V20a1 1 0 0 1-1 1A17 17 0 0 1 3 4a1 1 0 0 1 1-1h3.5a1 1 0 0 1 1 1c0 1.25.2 2.45.57 3.57a1 1 0 0 1-.25 1z"/></svg>
        (555) 214-0390
      </li>
      <li class="contacts__item">
        <svg class="contacts__icon" viewBox="0 0 24 24" aria-hidden="true"><path d="M3 8c0-2 4-4 9-4s9 2 9 4v2h-5V8H8v2H3z"/><path d="M6 12h12l2 8H4z"/></svg>
        1-800-555-0147
      </li>
      <li class="contacts__item">
        <svg class="contacts__icon" viewBox="0 0 24 24" aria-hidden="true"><path d="M2 5h20v14H2z"/><path d="M2 5l10 8 10-8" fill="none" stroke="#fff" stroke-width="1.6"/></svg>
        info@ridgelinebuild.com
      </li>
      <li class="contacts__item">
        <svg class="contacts__icon" viewBox="0 0 24 24" aria-hidden="true"><circle cx="12" cy="12" r="10"/><path d="M2 12h20M12 2c3 3 3 17 0 20M12 2c-3 3-3 17 0 20" fill="none" stroke="#fff" stroke-width="1.4"/></svg>
        www.ridgelinebuild.com
      </li>
    </ul>
  </section>

  <section class="card card--back" aria-label="Business card back">
    <div class="company">
      <span class="company__name">Ridgeline</span>
      <span class="company__tag">Design + Build</span>
    </div>
  </section>

</main>
</body>
</html>
```